Web design for business website

I need a web design for a business website for one of our clients who is specialized in alarm management software. I would like you to design 3 web pages, one for each of the 3 pages. You need to process the corporate identity of our client to the web design. This means the colors of the logo (red and black) should definitely show up on all of the 3 pages. Find the logo file for the logo of our customer. To increase readability I suggest you use a white/light background. All suggestions are welcome.

Please kindly download atttached Webdesign.zip and read the project brief first. The project brief refers to all other files of the zip file. Your design must have exactly the same structure as the wireframes.
Updates

Target Market(s)

B2B, Alarm management

Industry/Entity Type

Business

Number of Pages Required

3 page

Requirements
Must have
• The web design must have exactly the same structure as the wireframes and needs to contain the colors of the company logo.

```html
<!DOCTYPE html>
<html lang="en">
<head>
<meta charset="utf-8">
<title>LOGIRA – Real-time reasoning solutions</title>
<link href="https://fonts.googleapis.com/css2?family=Raleway:wght@300;400;500;700;800&family=Roboto:wght@400;500&display=swap" rel="stylesheet">
<style>
:root{
  --blush:#f0e1dd;
  --navy:#1b1a2e;
  --navy-deep:#17162a;
  --navy-panel:#2b2847;
  --navy-active:#2e2b4c;
  --red:#c0381a;
  --red-dark:#a52f17;
  --logo-red:#c9361a;
  --ink:#222;
  --muted:#666;
  --white:#fff;
  --footer-text:#c9c9d3;
}
*{margin:0;padding:0;box-sizing:border-box}
html,body{width:1037px;height:1200px;overflow:hidden;background:var(--white)}
body{position:relative;font-family:'Roboto',sans-serif;color:var(--ink)}
.abs{position:absolute}

.topbar{left:0;top:0;width:1037px;height:35px;background:var(--blush)}
.topbar .call{left:96px;top:12px;font-size:10px;color:#333}
.lang{left:720px;top:12px;width:23px;height:14px;background:var(--navy);border:2px solid var(--red)}
.lang-caret{left:748px;top:12px;font-size:8px;color:#999}
.search{left:768px;top:5px;width:172px;height:27px;background:#fff;border:1px solid #ddd;font-size:10px;color:#999;padding:8px 10px}
.search svg{position:absolute;right:8px;top:8px}

.header{left:0;top:35px;width:1037px;height:84px;background:var(--white)}
.brand-mark{left:96px;top:57px;width:42px;height:42px;border-radius:50%;background:var(--logo-red)}
.brand-name{left:149px;top:58px;font-family:'Raleway',sans-serif;font-weight:800;font-size:30px;letter-spacing:2px;color:var(--navy)}
.brand-tag{left:150px;top:89px;font-size:9px;color:#333;letter-spacing:.3px}
.btn{top:61px;height:35px;width:80px;border:1px solid #e3c9c2;background:#fbf6f4;color:var(--red);font-size:10px;display:flex;align-items:center;justify-content:center}

.nav{left:0;top:119px;width:1037px;height:47px;background:var(--navy)}
.nav-item{top:119px;height:47px;display:flex;align-items:center;justify-content:center;font-family:'Raleway',sans-serif;font-size:11px;color:var(--white)}
.nav-item.active{background:var(--navy-active)}

.hero{left:0;top:166px;width:1037px;height:418px;background:linear-gradient(180deg,#8a8d95 0%,#c9a56a 30%,#e4a94a 48%,#5c5b4d 62%,#3c4a2e 78%,#2a3120 100%)}
.hero-arrow{top:365px;width:18px;height:18px;border-radius:50%;background:#3a3a3a;display:flex;align-items:center;justify-content:center}

.dropdown{left:203px;top:166px;width:327px;height:121px;background:var(--navy-panel)}
.dropdown-img{left:218px;top:185px;width:176px;height:85px;background:linear-gradient(135deg,#2a4e7a,#c9a23c 55%,#4b7a8e)}
.dropdown-link{left:407px;font-family:'Raleway',sans-serif;font-size:10px;color:var(--white)}

.welcome-title{left:0;top:606px;width:1037px;text-align:center;font-family:'Raleway',sans-serif;font-weight:400;font-size:24px;color:var(--ink)}
.welcome-text{left:94px;top:640px;width:848px;text-align:center;font-size:9.6px;line-height:22.2px;color:var(--muted)}

.clients{left:0;top:778px;width:1037px;height:118px;background:var(--blush)}
.clients-title{left:0;top:797px;width:1037px;text-align:center;font-family:'Raleway',sans-serif;font-size:23px;color:var(--ink)}
.client{top:842px;height:24px;display:flex;align-items:center;gap:6px;font-family:'Raleway',sans-serif;font-weight:700;font-size:15px;color:#3a3a4a}
.client i{display:block;width:14px;height:14px;border-radius:50%;background:var(--red)}

.signup{left:0;top:896px;width:1037px;height:61px;background:var(--red)}
.social{top:920px;width:14px;height:14px;border-radius:50%;background:var(--white)}
.email{left:556px;top:907px;width:217px;height:41px;background:var(--red-dark);color:#f0c7bb;font-size:11px;padding:14px 13px}
.subscribe{left:785px;top:907px;width:155px;height:41px;background:var(--navy);color:var(--white);font-family:'Raleway',sans-serif;font-size:14px;display:flex;align-items:center;justify-content:center}

.footer{left:0;top:957px;width:1037px;height:196px;background:var(--navy)}
.col{top:980px}
.col h3{font-family:'Raleway',sans-serif;font-weight:400;font-size:14px;color:var(--white);margin-bottom:6px}
.col ul{list-style:none}
.col li{font-size:9.6px;color:var(--footer-text);height:29.6px;display:flex;align-items:center;gap:6px}
.col li::before{content:"";width:6px;height:6px;border:1.5px solid var(--red);flex:none}
.divider{top:978px;width:1px;height:175px;background:#26253a}
.contact li::before{display:none}
.contact li{align-items:flex-start;height:auto;margin-bottom:12px;line-height:18px}
.contact svg{flex:none;margin-top:2px}

.bottom{left:0;top:1153px;width:1037px;height:47px;background:var(--navy-deep)}
.copyright{left:0;top:1172px;width:1037px;text-align:center;font-size:9px;color:#45445a}
</style>
</head>
<body>

<div class="abs topbar"></div>
<div class="abs call topbar"></div>
<div class="abs call" style="left:96px;top:12px;font-size:10px;color:#333">CALL US : &nbsp;+31 (0)20 555 0184</div>
<div class="abs lang" role="img" aria-label="Language selector"></div>
<div class="abs lang-caret">&#8964;</div>
<div class="abs search">Search...
  <svg width="10" height="10" viewBox="0 0 10 10"><circle cx="4" cy="4" r="3" fill="none" stroke="#999" stroke-width="1.3"/><line x1="6.3" y1="6.3" x2="9" y2="9" stroke="#999" stroke-width="1.3"/></svg>
</div>

<div class="abs header"></div>
<div class="abs brand-mark"></div>
<div class="abs brand-name">LOGIRA</div>
<div class="abs brand-tag">Real-time reasoning solutions</div>
<div class="abs btn" style="left:683px">ACCOUNT</div>
<div class="abs btn" style="left:772px">LOG IN</div>
<div class="abs btn" style="left:861px">SIGN UP</div>

<div class="abs nav"></div>
<div class="abs nav-item" style="left:112px;width:60px">Home</div>
<div class="abs nav-item active" style="left:203px;width:94px">Industry</div>
<div class="abs nav-item" style="left:331px;width:70px">Telecom</div>
<div class="abs nav-item" style="left:447px;width:60px">Power</div>
<div class="abs nav-item" style="left:549px;width:70px">Utilities</div>
<div class="abs nav-item" style="left:657px;width:60px">Infra</div>
<div class="abs nav-item" style="left:755px;width:60px">Store</div>

<div class="abs hero" role="img" aria-label="Refinery skyline at sunset reflected in a marsh"></div>
<div class="abs hero-arrow" style="left:28px"><svg width="8" height="8" viewBox="0 0 8 8"><path d="M5.5 1 2.5 4 5.5 7" fill="none" stroke="#ccc" stroke-width="1.5"/></svg></div>
<div class="abs hero-arrow" style="left:988px"><svg width="8" height="8" viewBox="0 0 8 8"><path d="M2.5 1 5.5 4 2.5 7" fill="none" stroke="#ccc" stroke-width="1.5"/></svg></div>

<div class="abs dropdown"></div>
<div class="abs dropdown-img" role="img" aria-label="Industrial plant lit up at night"></div>
<div class="abs dropdown-link" style="top:185px">Alarm Management</div>
<div class="abs dropdown-link" style="top:209px">Asset Management</div>
<div class="abs dropdown-link" style="top:233px">Predictive Maintenance</div>
<div class="abs dropdown-link" style="top:257px">Logic Design</div>

<h1 class="abs welcome-title">Welcome To &nbsp;Logira</h1>
<p class="abs welcome-text">Companies have invested to get data out of processes. New technologies have been developed to get real-time data out of the harshest places, like oil-well drill heads or the Great Barrier Riff. Data in itself means nothing without the context the data is collected in. Example: data from equipment under maintenance does not provide information to operations. Information - data which is valid and meaningful - can overwhelm any user without the proper knowledge to interpret this information. Logira technology enables easy application of such knowledge in a comprehensible – visual – representation and makes hypothetical reasoning with information possible providing meaningful advisories to subscribers when they need it or when it is required that they are made aware of a situation which requires their attention.</p>

<div class="abs clients"></div>
<h2 class="abs clients-title">Our Clients</h2>
<div class="abs client" style="left:103px"><i></i>Nordhaven</div>
<div class="abs client" style="left:263px">Polymara</div>
<div class="abs client" style="left:430px">Brouwvast</div>
<div class="abs client" style="left:597px"><i></i>Veltrix</div>
<div class="abs client" style="left:703px"><i></i>Sunmere</div>
<div class="abs client" style="left:793px"><i></i>Corvane</div>
<div class="abs client" style="left:882px">Qasira</div>

<div class="abs signup"></div>
<div class="abs social" style="left:96px" role="img" aria-label="Social network link"></div>
<div class="abs social" style="left:118px" role="img" aria-label="Video channel link"></div>
<div class="abs social" style="left:142px" role="img" aria-label="Microblog link"></div>
<div class="abs social" style="left:175px" role="img" aria-label="Professional network link"></div>
<div class="abs email">Enter Your Email Address</div>
<div class="abs subscribe">SUBSCRIBE</div>

<div class="abs footer"></div>
<div class="abs divider" style="left:233px"></div>
<div class="abs divider" style="left:359px"></div>
<div class="abs divider" style="left:507px"></div>
<div class="abs divider" style="left:672px"></div>

<div class="abs col" style="left:96px"><h3>Solutions</h3><ul><li>KORA Alarm Reporting</li><li>KORA Alarm Analysis</li><li>KORA Alarm Expert</li><li>USE</li></ul></div>
<div class="abs col" style="left:266px"><h3>Industries</h3><ul><li>Industry</li><li>Telecom</li><li>Power</li><li>Utilities</li><li>Infra</li></ul></div>
<div class="abs col" style="left:401px"><h3>About us</h3><ul><li>Company</li><li>Overview</li><li>Leadership</li><li>Partners</li><li>Locations</li></ul></div>
<div class="abs col" style="left:541px"><h3>News</h3><ul><li>Product News</li><li>Partner News</li><li>Events</li><li>Press Releases</li><li>Vacancies</li></ul></div>
<div class="abs col contact" style="left:719px"><h3 style="margin-bottom:14px">Contact Us</h3><ul>
  <li><svg width="10" height="12" viewBox="0 0 10 12"><path d="M5 0a4 4 0 0 1 4 4c0 3-4 8-4 8S1 7 1 4a4 4 0 0 1 4-4z" fill="var(--red)"/><circle cx="5" cy="4" r="1.5" fill="var(--navy)"/></svg><span>123 45, Lorem Ipsm, Lorem Ipsm<br>Lorem Ipsm - 123 456</span></li>
  <li><svg width="12" height="10" viewBox="0 0 12 10"><rect width="12" height="10" fill="var(--red)"/><path d="M0 0 6 5 12 0" fill="none" stroke="var(--navy)"/></svg><span>info@domainname.com</span></li>
  <li><svg width="12" height="12" viewBox="0 0 12 12"><rect width="12" height="12" rx="2" fill="var(--red)"/><path d="M3.5 3c0 3 2.5 5.5 5.5 5.5" fill="none" stroke="var(--navy)" stroke-width="1.5"/></svg><span>123 456 789</span></li>
  <li><svg width="12" height="12" viewBox="0 0 12 12"><path d="M12 0 0 5l5 2 2 5z" fill="var(--red)"/></svg><span>Our Locations</span></li>
</ul></div>

<div class="abs bottom"></div>
<div class="abs copyright">(c) 2105 LOGIRA. All Right Reserved.</div>

</body>
</html>
```